RW Holloway LLC Business Card - Civil Engineering & Consulting Firm

We need a Business Card that is elegant, and masculine.  It is our Professional Civil Engineering & Consulting Company located in San Antonio TX (Not s construction or builder firm- no gears & no tool images please). We provide civil engineering services including  commercial site plans, grading and drainage plans, utility plans, hydraulics and hydrology, land planning, utility coordination, and other general civil engineering services related to commercial and residential development.
We have 2 existing Logos. We would like to convey reliability, strength, trustworthiness and attention to detail.  Blues and orange tones as per logo We are OK with the use of a darker blue in the mix.  We have 2 logo versions - Full Company Name Logo to go on the back of card, & Small Icon Logo for the front w/ personal Info.

Target Market(s)
Architects, Real Estate Developers, Other Strctural Engineers, Surveyers, General Contractors
Industry/Entity Type
Professional Civil Engineering
Contact Information for Business Card
Name, Position, Address, Cell & Office #, email, and company website
Font styles to use
Other font styles liked:
- Avian
Requirements
Should not have
- No Tools, No Gears, no Cranes, or Construction Equipment.

```html
<!DOCTYPE html>
<html lang="en">
<head>
<meta charset="utf-8">
<title>RW Holloway LLC – Business Card</title>
<link rel="stylesheet" href="https://fonts.googleapis.com/css2?family=Montserrat:wght@400;500;700;800&display=swap">
<style>
  :root {
    --sky: #7aaed8;
    --amber: #e8913a;
    --amber-soft: #d9a275;
    --ink: #1f1f1f;
    --paper: #f7f7f7;
    --stage: #d4d4d4;
  }
  * { margin: 0; padding: 0; box-sizing: border-box; }
  html, body { width: 1200px; height: 900px; overflow: hidden; }
  body {
    background: var(--stage);
    font-family: "Montserrat", sans-serif;
    position: relative;
  }
  .card {
    position: absolute;
    width: 630px;
    height: 360px;
    border-radius: 28px;
    overflow: hidden;
    box-shadow: 0 10px 28px rgba(0,0,0,0.22);
  }

  /* Back of card */
  .card-back {
    left: 90px; top: 50px;
    background: linear-gradient(155deg, var(--sky) 0%, #a6abb2 45%, var(--amber-soft) 70%, var(--amber) 100%);
    display: flex;
    flex-direction: column;
    align-items: center;
    justify-content: center;
    color: #fff;
  }
  .company-name {
    display: flex;
    align-items: center;
    gap: 16px;
    font-weight: 500;
    font-size: 46px;
    letter-spacing: 1px;
    white-space: nowrap;
  }
  .company-mark { width: 26px; height: 26px; background: #fff; flex: none; }
  .company-tagline {
    margin-top: 14px;
    font-weight: 400;
    font-size: 17px;
    letter-spacing: 9px;
    white-space: nowrap;
  }

  /* Front of card */
  .card-front {
    left: 480px; top: 490px;
    background: var(--paper);
  }
  .header-art {
    position: absolute;
    left: 0; top: 0;
    width: 100%; height: 150px;
    background: linear-gradient(100deg, var(--amber) 0%, var(--amber-soft) 40%, var(--sky) 100%);
  }
  .holder { position: absolute; left: 40px; top: 42px; color: #fff; white-space: nowrap; }
  .holder-name { font-weight: 800; font-size: 24px; letter-spacing: 1px; }
  .holder-role { font-weight: 400; font-size: 18px; margin-top: 4px; }
  .address {
    position: absolute; left: 120px; top: 178px;
    font-weight: 500; font-size: 16px; line-height: 22px; color: var(--ink);
    white-space: nowrap;
  }
  .contacts {
    position: absolute; left: 120px; top: 234px;
    list-style: none;
    font-weight: 500; font-size: 16px; color: var(--ink);
    white-space: nowrap;
  }
  .contacts li { display: flex; align-items: center; gap: 12px; height: 24px; }
  .contacts svg { width: 18px; height: 18px; flex: none; }
  .front-brand {
    position: absolute; left: 390px; top: 200px;
    display: flex; align-items: center; gap: 10px;
    color: var(--amber);
    font-weight: 500; font-size: 22px;
    white-space: nowrap;
  }
  .front-brand .company-mark { width: 16px; height: 16px; background: var(--sky); }
</style>
</head>
<body>

  <section class="card card-back" aria-label="Business card back">
    <div class="company-name"><span class="company-mark"></span>RW Holloway LLC</div>
    <div class="company-tagline">CONSULTING ENGINEERS</div>
  </section>

  <section class="card card-front" aria-label="Business card front">
    <div class="header-art" role="img" aria-label="Decorative orange and blue sweeping header artwork"></div>

    <div class="holder">
      <p class="holder-name">DARREN KELLOWAY</p>
      <p class="holder-role">Co-Founder</p>
    </div>

    <p class="address">4120 N. Ridge Avenue<br>Suite 210 Alamo 27</p>

    <ul class="contacts">
      <li>
        <svg viewBox="0 0 20 20"><circle cx="10" cy="10" r="10" fill="#e8913a"/><path d="M6 5 L8.5 5 L9.5 8 L8 9 C8.7 10.6 9.4 11.3 11 12 L12 10.5 L15 11.5 L15 14 C10 14.5 5.5 10 6 5 Z" fill="#fff"/></svg>
        555-201-4410
      </li>
      <li>
        <svg viewBox="0 0 20 20"><circle cx="10" cy="10" r="10" fill="#e8913a"/><rect x="5" y="8" width="10" height="6" rx="1" fill="#fff"/><rect x="6" y="5.5" width="8" height="2" rx="1" fill="#fff"/></svg>
        555-201-4427
      </li>
      <li>
        <svg viewBox="0 0 20 20"><circle cx="10" cy="10" r="10" fill="#e8913a"/><rect x="5" y="6.5" width="10" height="7" fill="#fff"/><path d="M5 6.5 L10 10.5 L15 6.5" fill="none" stroke="#e8913a" stroke-width="1"/></svg>
        info@rwhollowayllc
      </li>
      <li>
        <svg viewBox="0 0 20 20"><circle cx="10" cy="10" r="10" fill="#e8913a"/><circle cx="10" cy="10" r="5" fill="none" stroke="#fff" stroke-width="1.3"/><path d="M5 10 H15 M10 5 C7.5 8 7.5 12 10 15 C12.5 12 12.5 8 10 5" fill="none" stroke="#fff" stroke-width="1"/></svg>
        www.hollowaycivil.com
      </li>
    </ul>

    <div class="front-brand"><span class="company-mark"></span>RW Holloway LLC</div>
  </section>

</body>
</html>
```